Looking for business card/letterhead/email signature

Take existing logo and create full design suite of collateral

Contact Information for Business Card

Use mock details that can be edited by us

Font styles to use
Sans Serif

```html
<!DOCTYPE html>
<html lang="en">
<head>
<meta charset="utf-8">
<title>Harlow Digital – Stationery Suite</title>
<link href="https://fonts.googleapis.com/css2?family=Arimo:wght@400;700&family=Didact+Gothic&display=swap" rel="stylesheet">
<style>
  :root{
    --brand-blue:#0b4d90;
    --paper:#f8f8f8;
    --backdrop:#e5e5e5;
    --ink:#4a4a4a;
    --ink-soft:#777;
    --white:#ffffff;
    --sign-blue:#6d8fc4;
  }
  *{box-sizing:border-box;margin:0;padding:0}
  html,body{width:1200px;height:796px;overflow:hidden}
  body{background:var(--backdrop);position:relative;font-family:"Arimo",Arial,sans-serif;color:var(--ink)}

  .piece{position:absolute;background:var(--paper);overflow:hidden;border:1px solid #dcdcdc}
  .wordmark{font-family:"Arimo",Arial,sans-serif;font-weight:700;color:var(--brand-blue);line-height:1;letter-spacing:-.01em}
  .wordmark--light{color:var(--white)}

  /* Letterhead */
  .letterhead{left:342px;top:78px;width:336px;height:472px}
  .letterhead__band{position:absolute;left:82px;top:29px;right:0;height:45px;background:var(--brand-blue);color:var(--white);font-size:4.6px;line-height:1.45}
  .letterhead__col{position:absolute;top:15px}
  .letterhead__col--address{left:42px}
  .letterhead__col--phone{left:118px;padding-left:8px;border-left:.6px solid rgba(255,255,255,.8)}
  .letterhead__col--mail{left:168px;padding-left:8px;border-left:.6px solid rgba(255,255,255,.8)}
  .letterhead__logo{position:absolute;left:30px;top:38px;font-size:12.5px}
  .letterhead__greeting{position:absolute;left:30px;top:135px;font-family:"Didact Gothic",sans-serif;font-size:8px;color:var(--ink)}
  .letterhead__body{position:absolute;left:30px;top:158px;width:278px;font-family:"Didact Gothic",sans-serif;font-size:4.4px;line-height:1.62;color:var(--ink-soft);text-align:justify}
  .letterhead__body p{margin-bottom:7px}
  .letterhead__closing{position:absolute;left:30px;top:308px;font-family:"Didact Gothic",sans-serif;font-size:4.6px;color:var(--ink-soft)}
  .letterhead__signature{position:absolute;left:28px;top:326px;width:64px;height:28px;background:linear-gradient(90deg,rgba(109,143,196,.25),rgba(109,143,196,.1));border-radius:3px}
  .letterhead__web{position:absolute;left:0;right:0;top:452px;text-align:center;font-size:4.6px;letter-spacing:.35em;color:var(--ink-soft)}

  /* Folder */
  .folder{left:706px;top:50px;width:396px;height:500px;background:var(--brand-blue);border:none}
  .folder__spine{position:absolute;top:0;bottom:0;width:1px;background:rgba(255,255,255,.22)}
  .folder__band{position:absolute;left:250px;top:198px;width:146px;height:104px;background:var(--white);border-radius:52px 0 0 52px}
  .folder__logo{position:absolute;right:152px;top:228px;font-size:22px;text-align:right;line-height:1.05}

  /* Business card back (reused at two sizes) */
  .card-back{width:305px;height:147px;position:absolute;background:var(--paper);overflow:hidden;border:1px solid #dcdcdc}
  .card-back--large{left:42px;top:606px}
  .card-back--small{left:158px;top:461px;transform:scale(.503);transform-origin:0 0}
  .card-back__field{position:absolute;left:86px;top:0;right:0;bottom:0;background:var(--brand-blue)}
  .card-back__disc{position:absolute;left:6px;top:-6px;width:160px;height:160px;border-radius:50%;background:var(--paper)}
  .card-back__logo{position:absolute;left:26px;top:52px;font-size:21px;line-height:1.05}
  .card-back__details{position:absolute;right:23px;top:19px;text-align:right;color:var(--white);font-size:7.2px;line-height:8.9px}
  .card-back__name{font-size:9.6px;font-weight:700;line-height:10px}
  .card-back__title{font-size:7.2px;line-height:9px;margin-bottom:25px}
  .card-back__row{display:flex;justify-content:flex-end;align-items:center;gap:4px;height:8.9px}
  .icon{width:6px;height:6px;fill:var(--white);flex:none}

  /* Business card front */
  .card-front{left:157px;top:357px;width:153px;height:88px}
  .card-front__logo{position:absolute;left:0;right:0;top:30px;text-align:center;font-size:12.5px;line-height:1.05}
  .card-front__web{position:absolute;left:0;right:0;bottom:8px;text-align:center;font-size:3.6px;letter-spacing:.3em;color:var(--ink-soft)}

  /* Envelope front */
  .envelope{left:369px;top:580px;width:386px;height:176px}
  .envelope__band{position:absolute;left:96px;top:20px;right:0;height:50px;background:var(--brand-blue)}
  .envelope__address{position:absolute;right:30px;top:18px;text-align:right;color:var(--white);font-size:4.6px;line-height:1.45}
  .envelope__logo{position:absolute;left:22px;top:30px;font-size:13px;line-height:1.05}

  /* Envelope back */
  .envelope-back{left:774px;top:578px;width:386px;height:176px}
  .envelope-back__flap{position:absolute;left:0;top:0;width:386px;height:56px}
  .envelope-back__logo{position:absolute;left:0;right:0;top:22px;text-align:center;font-size:9px;line-height:1.05}
</style>
</head>
<body>

<!-- Letterhead -->
<section class="piece letterhead">
  <div class="letterhead__logo wordmark">Harlow<br>Digital</div>
  <div class="letterhead__band">
    <div class="letterhead__col letterhead__col--address">214 Cedar Hollow Road<br>Juneau, Alaska 99801</div>
    <div class="letterhead__col letterhead__col--phone">555 210 4471<br>555 318 0926</div>
    <div class="letterhead__col letterhead__col--mail">555 642 7783<br>evan@harlowdigital.net</div>
  </div>
  <p class="letterhead__greeting">Dear Ms. Reyes,</p>
  <div class="letterhead__body">
    <p>Thank you for meeting with our team last week. We enjoyed learning about your plans for the coming season and the goals you shared for your new storefront. This letter confirms the scope we discussed together, including the brand refresh, the printed stationery and a simple website that your staff can update.</p>
    <p>Our first step is a short discovery session with your managers. We will review current materials, gather feedback from customers and outline the tone of voice that fits your business. A written summary will follow within two weeks of that session.</p>
    <p>Next we will prepare two design directions for your review, each shown on cards, letters, envelopes and folders. You may combine ideas from both. Once a direction is chosen we will refine the details, prepare final files and arrange printing with a trusted local partner.</p>
    <p>Please let us know if any part of this plan needs changes. We look forward to working with you and your team in the months ahead.</p>
  </div>
  <p class="letterhead__closing">Sincerely,</p>
  <div class="letterhead__signature" role="img" aria-label="Handwritten signature of the sender"></div>
  <p class="letterhead__web">www.harlowdigital.net</p>
</section>

<!-- Presentation folder -->
<section class="piece folder">
  <span class="folder__spine" style="left:5px"></span>
  <span class="folder__spine" style="left:10px"></span>
  <span class="folder__spine" style="left:22px"></span>
  <div class="folder__band"></div>
  <div class="folder__logo wordmark wordmark--light">Harlow<br>Digital</div>
</section>

<!-- Business card front -->
<section class="piece card-front">
  <div class="card-front__logo wordmark">Harlow<br>Digital</div>
  <p class="card-front__web">www.harlowdigital.net</p>
</section>

<!-- Business card back, small and large -->
<section class="card-back card-back--small">
  <div class="card-back__field"></div>
  <div class="card-back__disc"></div>
  <div class="card-back__logo wordmark">Harlow<br>Digital</div>
  <div class="card-back__details">
    <div class="card-back__name">EVAN MARSH</div>
    <div class="card-back__title">CEO/FOUNDER</div>
    <div>214 Cedar Hollow Road</div>
    <div>Juneau, Alaska 99801</div>
    <div class="card-back__row">555 210 4471 <svg class="icon" viewBox="0 0 10 10"><path d="M2 1l2 2-1 1.3a6 6 0 0 0 2.7 2.7L7 6l2 2-1.3 1.4C4.5 9.3.7 5.5.6 2.3z"/></svg></div>
    <div class="card-back__row">555 318 0926 <svg class="icon" viewBox="0 0 10 10"><path d="M3 .5h4a.8.8 0 0 1 .8.8v7.4a.8.8 0 0 1-.8.8H3a.8.8 0 0 1-.8-.8V1.3A.8.8 0 0 1 3 .5zm.4 1.2v6h3.2v-6z"/></svg></div>
    <div class="card-back__row">555 642 7783 <svg class="icon" viewBox="0 0 10 10"><path d="M2.5 1h5v2.5h-5zM1 4h8v3.5H7.5V9h-5V7.5H1zm2.5 2.5v1.5h3V6.5z"/></svg></div>
    <div class="card-back__row">evan@harlowdigital.net <svg class="icon" viewBox="0 0 10 10"><path d="M.5 2h9v6h-9zm1 1v.3L5 5.6l3.5-2.3V3z"/></svg></div>
    <div class="card-back__row">www.harlowdigital.net <svg class="icon" viewBox="0 0 10 10"><path d="M5 .5a4.5 4.5 0 1 0 0 9 4.5 4.5 0 0 0 0-9zm0 1a3.5 3.5 0 0 1 3.4 2.7H6.6A6 6 0 0 0 5 1.5zm0 7a3.5 3.5 0 0 1-3.4-2.7h1.8A6 6 0 0 0 5 8.5z"/></svg></div>
  </div>
</section>

<section class="card-back card-back--large">
  <div class="card-back__field"></div>
  <div class="card-back__disc"></div>
  <div class="card-back__logo wordmark">Harlow<br>Digital</div>
  <div class="card-back__details">
    <div class="card-back__name">EVAN MARSH</div>
    <div class="card-back__title">CEO/FOUNDER</div>
    <div>214 Cedar Hollow Road</div>
    <div>Juneau, Alaska 99801</div>
    <div class="card-back__row">555 210 4471 <svg class="icon" viewBox="0 0 10 10"><path d="M2 1l2 2-1 1.3a6 6 0 0 0 2.7 2.7L7 6l2 2-1.3 1.4C4.5 9.3.7 5.5.6 2.3z"/></svg></div>
    <div class="card-back__row">555 318 0926 <svg class="icon" viewBox="0 0 10 10"><path d="M3 .5h4a.8.8 0 0 1 .8.8v7.4a.8.8 0 0 1-.8.8H3a.8.8 0 0 1-.8-.8V1.3A.8.8 0 0 1 3 .5zm.4 1.2v6h3.2v-6z"/></svg></div>
    <div class="card-back__row">555 642 7783 <svg class="icon" viewBox="0 0 10 10"><path d="M2.5 1h5v2.5h-5zM1 4h8v3.5H7.5V9h-5V7.5H1zm2.5 2.5v1.5h3V6.5z"/></svg></div>
    <div class="card-back__row">evan@harlowdigital.net <svg class="icon" viewBox="0 0 10 10"><path d="M.5 2h9v6h-9zm1 1v.3L5 5.6l3.5-2.3V3z"/></svg></div>
    <div class="card-back__row">www.harlowdigital.net <svg class="icon" viewBox="0 0 10 10"><path d="M5 .5a4.5 4.5 0 1 0 0 9 4.5 4.5 0 0 0 0-9zm0 1a3.5 3.5 0 0 1 3.4 2.7H6.6A6 6 0 0 0 5 1.5zm0 7a3.5 3.5 0 0 1-3.4-2.7h1.8A6 6 0 0 0 5 8.5z"/></svg></div>
  </div>
</section>

<!-- Envelope front -->
<section class="piece envelope">
  <div class="envelope__band">
    <div class="envelope__address">214 Cedar Hollow Road<br>Juneau, Alaska 99801</div>
  </div>
  <div class="envelope__logo wordmark">Harlow<br>Digital</div>
</section>

<!-- Envelope back -->
<section class="piece envelope-back">
  <svg class="envelope-back__flap" viewBox="0 0 386 56" aria-hidden="true">
    <path d="M0 0H386V8Q386 18 378 32Q368 56 346 56H40Q18 56 8 32Q0 18 0 8Z" fill="var(--brand-blue)"/>
  </svg>
  <div class="envelope-back__logo wordmark wordmark--light">Harlow<br>Digital</div>
</section>

</body>
</html>
```